Tessmar Fahrwerkstatt
Sehr angenehme zusammenarbeit nicht aufdringlich und genau auf die Wünsche eingegangen. Wir werde sicher noch mehr zusammen Arbeiten. Gruss Lukas Hegemann Inhaber Tessmar Fahrwerkstatt
Zielgruppe
Dinks und Kunden mit viel Erfolg und hohem Ausgabepotential.
Aufgabenstellung
Unsere Firma vertreibt Fahrzeuge im Luxusbereich hauptgebiet Valmerra aber auch andere Sportwagen. Was uns fehlt ist ein optischer Wiedererkennugswert. Deshalb hätten wir gerne ein Visitenkarten Design und Briefpapier Design. Später soll auch noch eine Webseite mit gleichem Wiedererkennungswert entstehen. " Roter Faden "

```html
<!DOCTYPE html>
<html lang="de">
<head>
<meta charset="utf-8">
<title>Tessmar Fahrwerkstatt – Visitenkarte</title>
<link href="https://fonts.googleapis.com/css2?family=Fira+Sans:wght@400;500&display=swap" rel="stylesheet">
<style>
  :root {
    --stage: #000000;
    --card: #4f4f4f;
    --card-light: #5c5c5c;
    --card-edge: #6a6a6a;
    --band: rgba(120, 120, 120, 0.55);
    --ink-dark: #151515;
    --ink-light: #f2f2f2;
    --ink-muted: #bdbdbd;
  }
  * { box-sizing: border-box; margin: 0; padding: 0; }
  html, body {
    width: 1200px; height: 744px; overflow: hidden;
    background: var(--stage);
    font-family: "Fira Sans", Arial, sans-serif;
  }
  .canvas { position: relative; width: 1200px; height: 744px; }
  .card {
    position: absolute; top: 194px;
    width: 548px; height: 364px;
    border-radius: 30px;
    background: radial-gradient(ellipse at 40% 35%, var(--card-light), var(--card) 75%);
    box-shadow: inset 0 0 0 1px var(--card-edge);
    overflow: hidden;
  }
  .card--front { left: 44px; }
  .card--back { left: 612px; }

  .brand {
    position: absolute;
    display: flex; align-items: center; gap: 14px;
    color: var(--ink-dark); font-weight: 500;
  }
  .brand__mark {
    width: 46px; height: 46px; border-radius: 50%;
    background: #3a3a3a;
    flex: none;
  }
  .card--front .brand {
    left: 0; right: 0; top: 150px; justify-content: center;
    font-size: 24px; letter-spacing: 1px; color: #333333;
  }
  .card--back .brand {
    right: 28px; top: 42px;
    font-size: 16px; line-height: 18px; letter-spacing: 0.5px;
  }
  .card--back .brand__mark { width: 40px; height: 40px; }

  .contact-band {
    position: absolute; left: 0; right: 0; top: 178px; height: 164px;
    background: var(--band);
    padding: 14px 22px 0 22px;
  }
  .person {
    font-size: 25px; font-weight: 500; line-height: 32px;
    color: var(--ink-dark); margin-bottom: 8px;
  }
  .person__surname { color: var(--ink-light); }
  .details {
    display: grid; grid-template-columns: 136px 160px auto;
    font-size: 16px; line-height: 23px; color: var(--ink-muted);
  }
  .details__label { color: var(--ink-dark); }
</style>
</head>
<body>
<main class="canvas">
  <section class="card card--front" aria-label="Vorderseite">
    <div class="brand">
      <span class="brand__mark"></span>
      <span class="brand__name">Tessmar Fahrwerkstatt</span>
    </div>
  </section>

  <section class="card card--back" aria-label="Rückseite">
    <div class="brand">
      <span class="brand__mark"></span>
      <span class="brand__name">TESSMAR<br>Fahrwerkstatt</span>
    </div>

    <div class="contact-band">
      <p class="person">Lukas <span class="person__surname">Hegemann</span></p>
      <div class="details">
        <div>
          <span class="details__label">Büro</span><br>
          Erlenweg 6<br>
          CH 8175 Rietholz
        </div>
        <div>
          <span class="details__label">Showroom</span><br>
          Talackerstrasse 7<br>
          CH 8642 Hallwies
        </div>
        <div>
          <span class="details__label">Mobil:</span> +41795550173<br>
          <span class="details__label">E-Mail:</span> info@tessmar.ch<br>
          www.tessmar.ch
        </div>
      </div>
    </div>
  </section>
</main>
</body>
</html>
```